Kestrada LLC, needs a web page no more than 5 pages (for now)

Kestrada is a general contractor. Our services include general contracting, design-build construction, disaster recovery and environmental remediation. Our main clients are PMX, TQ, State and Local Gov't Agencies, Hospitals and Schools. Kestrada is also a SDVOSB.

```html
<!DOCTYPE html>
<html lang="en">
<head>
<meta charset="utf-8">
<title>Kestrada — General Contracting &amp; Design-Build</title>
<link href="https://fonts.googleapis.com/css2?family=Lexend:wght@400;500&family=Questrial&display=swap" rel="stylesheet">
<style>
  :root{
    --black:#000;
    --ink:#0b0b0b;
    --panel:#141414;
    --gold:#d6a047;
    --white:#fff;
    --grey:#5a5a5a;
    --line:#4a4a4a;
  }
  *{margin:0;padding:0;box-sizing:border-box}
  html,body{width:1200px;height:3672px;overflow:hidden;background:var(--black)}
  body{position:relative;color:var(--white);font-family:"Questrial",sans-serif}
  .abs{position:absolute}
  .head{font-family:"Lexend",sans-serif;font-weight:500;text-transform:uppercase;letter-spacing:-.3px}
  .gold{color:var(--gold)}
  .btn{position:absolute;display:flex;align-items:center;justify-content:center;gap:12px;font-family:"Lexend",sans-serif;font-size:13.5px;text-transform:uppercase;color:var(--white);border:1px solid var(--white);height:40px}
  .btn.fill{background:var(--gold);border-color:var(--gold)}
  .btn svg{width:20px;height:10px}
  .photo{position:absolute}
  .rule{position:absolute;height:3px;background:var(--line)}

  /* nav */
  .nav{position:absolute;left:0;top:0;width:1200px;height:78px;background:var(--black)}
  .brand{position:absolute;display:flex;align-items:center;gap:10px;font-family:"Lexend",sans-serif;font-weight:500;color:var(--white)}
  .brand i{display:block;border:2px solid var(--gold);border-radius:50%}
  .nav-links{position:absolute;left:486px;top:33px;display:flex;gap:31px;font-family:"Lexend",sans-serif;font-size:13px}
  .nav-links a{color:var(--white);text-decoration:none}
  .nav-links a.active{color:var(--gold)}
  .search{position:absolute;left:1054px;top:25px;width:32px;height:32px;border:1px solid #555;border-radius:50%}

  /* hero */
  .hero-panel{position:absolute;left:0;top:78px;width:600px;height:515px;background:#151515;clip-path:polygon(0 0,100% 0,100% 453px,0 100%)}
  .hero-title{left:111px;top:176px;font-size:34px;line-height:57px}
  .hero-sub{left:111px;top:298px;font-size:18px;line-height:40px}

  /* about */
  .about-frame{position:absolute;left:221px;top:728px;width:312px;height:399px;border:4px solid var(--gold)}
  .about-text{left:717px;top:762px;width:374px;font-size:15px;line-height:32.6px}
  .about-text p+p{margin-top:16px}

  /* services */
  .svc{position:absolute;top:1367px;width:400px;height:481px}
  .svc-label{position:absolute;left:36px;bottom:34px;display:flex;align-items:center;gap:12px;font-size:19px}
  .svc-label svg{width:26px;height:12px}

  /* difference */
  .diff-intro{left:111px;top:2008px;width:970px;font-size:15.5px;line-height:33px}
  .card-title{font-size:18.5px}
  .card-text{font-size:15.5px;line-height:33px;width:460px}

  /* projects */
  .projects{position:absolute;left:0;top:2726px;width:1200px;height:623px;background:var(--panel)}
  .arrow{position:absolute;width:14px;height:18px}

  /* footer */
  .foot-title{font-size:23px}
  .foot-links{left:506px;top:3447px;font-family:"Lexend",sans-serif;font-size:13.5px;line-height:41.2px;list-style:none}
  .icon-dot{position:absolute;width:38px;height:38px;border-radius:50%;background:#262626;display:flex;align-items:center;justify-content:center}
  .foot-info{font-family:"Lexend",sans-serif;font-size:13.5px;line-height:31.5px;text-transform:uppercase}
</style>
</head>
<body>

<header class="nav">
  <div class="brand" style="left:111px;top:24px;font-size:24px"><i style="width:26px;height:26px"></i>KESTRADA</div>
  <nav class="nav-links">
    <a class="active" href="#">HOME</a><a href="#">ABOUT US</a><a href="#">SERVICES</a><a href="#">PROJECTS</a><a href="#">CLIENTS</a><a href="#">CONTACT</a>
  </nav>
  <div class="search">
    <svg viewBox="0 0 32 32" width="32" height="32"><circle cx="15" cy="15" r="3.5" fill="none" stroke="#fff" stroke-width="1.4"/><path d="M17.6 17.6l2.6 2.6" stroke="#fff" stroke-width="1.4"/></svg>
  </div>
</header>

<section>
  <div class="hero-panel"></div>
  <div class="photo" role="img" aria-label="Curved futuristic building with silver geometric panelled facade under blue sky" style="left:600px;top:78px;width:600px;height:515px;background:linear-gradient(160deg,#3e73b5 0%,#8fb0d6 35%,#d8dde3 60%,#a9b2bd 80%,#e9ecef 100%)"></div>
  <h1 class="abs head hero-title">Building trust.<br><span class="gold">Delivering excellence.</span></h1>
  <p class="abs hero-sub">General Contracting &amp; Design-Build Services for<br>Government, Healthcare, and Education</p>
  <a class="btn fill" style="left:111px;top:408px;width:163px">GET IN TOUCH <svg viewBox="0 0 20 10"><path d="M0 5h18M14 1l4 4-4 4" fill="none" stroke="#fff" stroke-width="1.3"/></svg></a>
</section>

<section>
  <div class="about-frame"></div>
  <div class="photo" role="img" aria-label="Recovery worker in orange safety jacket clearing debris from floodwater" style="left:111px;top:677px;width:318px;height:402px;background:linear-gradient(150deg,#7b6a55 0%,#3f4a52 45%,#c4722b 60%,#2b3138 100%)"></div>
  <div class="photo" role="img" aria-label="Modern house with wood-clad upper box and dark garage" style="left:323px;top:780px;width:318px;height:401px;background:linear-gradient(180deg,#dfe4e8 0%,#c9cfd4 25%,#8c5a33 45%,#3a3a3a 75%,#6f8b4e 100%)"></div>

  <div class="rule" style="left:717px;top:676px;width:61px"></div>
  <h2 class="abs head" style="left:717px;top:696px;font-size:31px">About <span class="gold">Kestrada</span></h2>
  <div class="abs about-text">
    <p>At Kestrada, we believe that construction is more than just building structures—it's about building trust, relationships, and lasting value for the communities we serve. As a Service-Disabled Veteran-Owned Small Business (SDVOSB), we bring the discipline, precision, and integrity of military service into every project.</p>
    <p>With proven experience in general contracting,<br>design-build construction, disaster recovery, and environmental remediation, we specialize in delivering high-quality solutions.</p>
  </div>
  <a class="btn" style="left:717px;top:1140px;width:140px">READ MORE <svg viewBox="0 0 20 10"><path d="M0 5h18M14 1l4 4-4 4" fill="none" stroke="#fff" stroke-width="1.3"/></svg></a>
</section>

<section>
  <div class="rule" style="left:111px;top:1286px;width:61px"></div>
  <h2 class="abs head" style="left:197px;top:1267px;font-size:31px">Kestrada <span class="gold">Services</span></h2>
  <a class="btn fill" style="left:916px;top:1267px;width:173px">VIEW SERVICES <svg viewBox="0 0 20 10"><path d="M0 5h18M14 1l4 4-4 4" fill="none" stroke="#fff" stroke-width="1.3"/></svg></a>

  <div class="svc" role="img" aria-label="Curved white modern building facade with ribbon windows" style="left:0;background:linear-gradient(160deg,#2f4a55 0%,#6c7f86 40%,#2a3236 75%,#0d0f10 100%)">
    <div class="svc-label head">Design-Build Construction <svg viewBox="0 0 26 12"><path d="M0 6h24M19 1l5 5-5 5" fill="none" stroke="#fff" stroke-width="1.6"/></svg></div>
  </div>
  <div class="svc" role="img" aria-label="Crews in safety vests clearing rubble beside a damaged building" style="left:400px;background:linear-gradient(170deg,#7d7a73 0%,#5c5850 40%,#3a3a35 75%,#111 100%)">
    <div class="svc-label head gold">Disaster Recovery <svg viewBox="0 0 26 12"><path d="M0 6h24M19 1l5 5-5 5" fill="none" stroke="#d6a047" stroke-width="1.6"/></svg></div>
  </div>
  <div class="svc" role="img" aria-label="Excavators and workers on a remediation site near an industrial plant" style="left:800px;background:linear-gradient(170deg,#8a9196 0%,#4f6a45 30%,#5c5546 55%,#2d2b27 80%,#0f0f0f 100%)">
    <div class="svc-label head">Environmental Remediation <svg viewBox="0 0 26 12"><path d="M0 6h24M19 1l5 5-5 5" fill="none" stroke="#fff" stroke-width="1.6"/></svg></div>
  </div>
</section>

<section>
  <div class="rule" style="left:111px;top:1931px;width:61px"></div>
  <h2 class="abs head" style="left:111px;top:1950px;font-size:31px">The Kestrada <span class="gold">Difference</span></h2>
  <p class="abs diff-intro">Harlowe is a premier construction services firm committed to building environments and&nbsp; experiences that enable our communities to<br>thrive. Our exceptionally talented team consistently delivers on our promise of complete project and customer satisfaction.</p>

  <div class="photo" role="img" aria-label="Three people reviewing plans inside a building under renovation" style="left:118px;top:2112px;width:456px;height:256px;border-radius:6px;background:linear-gradient(135deg,#8a7760 0%,#c9bfae 45%,#e6e0d6 70%,#9a8f80 100%)"></div>
  <h3 class="abs head gold card-title" style="left:118px;top:2402px">Proven Experience</h3>
  <p class="abs card-text" style="left:118px;top:2443px">With a strong record of performance across federal, state, and<br>institutional projects, we understand the unique compliance,<br>safety, and operational requirements our clients demand.</p>
  <a class="btn" style="left:118px;top:2570px;width:141px">READ MORE <svg viewBox="0 0 20 10"><path d="M0 5h18M14 1l4 4-4 4" fill="none" stroke="#fff" stroke-width="1.3"/></svg></a>

  <div class="photo" role="img" aria-label="Engineers in hi-vis vests reading drawings inside a steel-framed structure" style="left:624px;top:2142px;width:456px;height:256px;border-radius:6px;background:linear-gradient(160deg,#c9d3dc 0%,#7f8c97 40%,#c8d43a 55%,#56606a 75%,#2b3035 100%)"></div>
  <h3 class="abs head gold card-title" style="left:624px;top:2432px">Mission-Driven Approach</h3>
  <p class="abs card-text" style="left:624px;top:2473px">We treat every project with the same commitment and<br>precision that defined our service. From disaster recovery to<br>design-build facilities.</p>
  <a class="btn" style="left:624px;top:2600px;width:141px">READ MORE <svg viewBox="0 0 20 10"><path d="M0 5h18M14 1l4 4-4 4" fill="none" stroke="#fff" stroke-width="1.3"/></svg></a>
</section>

<section class="projects">
  <div class="rule" style="left:111px;top:58px;width:61px"></div>
  <h2 class="abs head" style="left:111px;top:78px;font-size:31px">Kestrada <span class="gold">Projects</span></h2>
  <p class="abs" style="left:111px;top:137px;font-size:16px">Check out and see what was deemed the greenest building in the nation!</p>
  <a class="btn" style="left:948px;top:86px;width:140px">READ MORE <svg viewBox="0 0 20 10"><path d="M0 5h18M14 1l4 4-4 4" fill="none" stroke="#fff" stroke-width="1.3"/></svg></a>

  <div class="photo" role="img" aria-label="Two site managers in hard hats discussing a steel-frame building under construction" style="left:111px;top:204px;width:978px;height:379px;border-radius:10px;background:linear-gradient(180deg,#9fc3e3 0%,#c6d8e6 30%,#6d6f70 55%,#b88a3a 75%,#8a8f93 100%)"></div>

  <svg class="arrow" style="left:42px;top:384px" viewBox="0 0 14 18"><path d="M10 2L3 9l7 7" fill="none" stroke="#fff" stroke-width="2"/></svg>
  <svg class="arrow" style="left:1134px;top:384px" viewBox="0 0 14 18"><path d="M4 2l7 7-7 7" fill="none" stroke="#fff" stroke-width="2"/></svg>
</section>

<footer>
  <div class="brand" style="left:111px;top:3452px;font-size:38px"><i style="width:40px;height:40px"></i>KESTRADA</div>
  <p class="abs" style="left:140px;top:3561px;font-family:'Lexend',sans-serif;font-size:15px">© 2025 KESTRADA, INC.</p>

  <h4 class="abs head gold foot-title" style="left:506px;top:3390px">Quick Links</h4>
  <ul class="abs foot-links">
    <li>HOME</li><li>ABOUT US</li><li>SERVICES</li><li>PROJECTS</li><li>CONTACT</li>
  </ul>

  <h4 class="abs head gold foot-title" style="left:812px;top:3390px">Contact Us</h4>
  <div class="icon-dot" style="left:812px;top:3444px">
    <svg viewBox="0 0 24 24" width="16" height="16"><path d="M6.6 10.8a15 15 0 006.6 6.6l2.2-2.2a1 1 0 011-.25 11.4 11.4 0 003.6.57 1 1 0 011 1V20a1 1 0 01-1 1A17 17 0 013 4a1 1 0 011-1h3.5a1 1 0 011 1c0 1.25.2 2.45.57 3.57a1 1 0 01-.25 1z" fill="#fff"/></svg>
  </div>
  <p class="abs foot-info" style="left:868px;top:3448px">(555) 318-2046</p>
  <div class="icon-dot" style="left:812px;top:3515px">
    <svg viewBox="0 0 24 24" width="16" height="16"><path d="M12 2a7 7 0 00-7 7c0 5.250 7 13 7 13s7-7.75 7-13a7 7 0 00-7-7zm0 9.5A2.5 2.5 0 1112 6.5a2.5 2.5 0 010 5z" fill="#fff"/></svg>
  </div>
  <p class="abs foot-info" style="left:868px;top:3518px">4180 Meridian Park Drive,<br>Suite 210<br>Alderbrook, TQ 40817</p>
</footer>

</body>
</html>
```